Design 4 pages for an event discovery website

This is a contest for the design of 4 pages for an events discovery website. The feature is part of the new sign-up process.

Please see the attached document for a full scope, mockups and the parent category icons.

Target Market(s)

18-35 Australian event goers

Industry/Entity Type

Events

Number of Pages Required

4 page

```html
<!DOCTYPE html>
<html lang="en">
<head>
<meta charset="utf-8">
<title>Venuora – Sign Up</title>
<link href="https://fonts.googleapis.com/css2?family=Oswald:wght@400;500&family=Roboto:wght@400;700&display=swap" rel="stylesheet">
<style>
  :root {
    --brand-blue: #2fa4e0;
    --btn-blue: #2a9fdc;
    --btn-orange: #f5953a;
    --btn-orange-light: #fbad5c;
    --text-dark: #333333;
    --nav-text: #444444;
    --error-red: #e02a2a;
    --panel-grey: rgba(150, 150, 165, 0.72);
    --benefits-blue: rgba(33, 120, 180, 0.78);
    --field-border: #d9d9d9;
    --footer-bg: #f2f2f2;
    --social-grey: #8a95a3;
  }
  * { box-sizing: border-box; margin: 0; padding: 0; }
  html, body { width: 1200px; height: 837px; overflow: hidden; }
  body { position: relative; font-family: "Roboto", sans-serif; color: var(--text-dark); background: #fff; }

  .site-header {
    position: absolute; left: 0; top: 0; width: 1200px; height: 115px;
    background: linear-gradient(#fdfdfd, #ececec);
  }
  .brand {
    position: absolute; left: 88px; top: 40px;
    font-family: "Roboto", sans-serif; font-weight: 700; font-size: 38px;
    color: var(--brand-blue); letter-spacing: 0.5px; line-height: 1;
  }
  .main-nav {
    position: absolute; left: 479px; top: 61px;
    font-size: 14px; color: var(--nav-text); letter-spacing: 0.3px;
  }
  .main-nav span.sep { margin: 0 12px; }
  .search-box {
    position: absolute; left: 621px; top: 46px; width: 236px; height: 44px;
    background: #fff; border: 1px solid #cfcfcf;
  }
  .search-box span { position: absolute; left: 15px; top: 13px; font-size: 14px; color: #555; }
  .search-box svg { position: absolute; right: 12px; top: 11px; }
  .header-btn {
    position: absolute; top: 47px; width: 114px; height: 42px;
    color: #fff; font-size: 16px; text-align: center; line-height: 42px; border-radius: 2px;
  }
  .header-btn.signup { left: 877px; background: linear-gradient(#38acea, #1f93d2); }
  .header-btn.login { left: 999px; top: 48px; background: linear-gradient(var(--btn-orange-light), var(--btn-orange)); }

  .hero {
    position: absolute; left: 0; top: 115px; width: 1200px; height: 607px;
    background:
      radial-gradient(ellipse at 25% 20%, rgba(200,90,140,0.55), transparent 45%),
      radial-gradient(ellipse at 75% 25%, rgba(120,170,210,0.7), transparent 55%),
      radial-gradient(ellipse at 50% 95%, rgba(10,15,30,0.9), transparent 60%),
      linear-gradient(#3a4c72, #1c2336);
  }

  .signup-panel {
    position: absolute; left: 87px; top: 169px; width: 375px; height: 499px;
    background: var(--panel-grey);
  }
  .panel-title {
    position: absolute; left: 23px; top: 24px;
    font-family: "Oswald", sans-serif; font-size: 33px; color: #fff; letter-spacing: -0.5px; line-height: 1;
  }
  .field {
    position: absolute; left: 24px; width: 222px; height: 41px;
    background: #fff; border: 1px solid var(--field-border); border-radius: 2px;
    font-size: 12.5px; color: #555; padding: 13px 0 0 12px;
  }
  .field.invalid { border-color: var(--error-red); }
  .error-msg {
    position: absolute; left: 256px; font-size: 12.5px; color: #fff;
  }
  .error-msg b { color: var(--error-red); font-weight: 400; margin-right: 6px; }
  .submit-btn {
    position: absolute; left: 24px; top: 431px; width: 222px; height: 47px;
    background: linear-gradient(var(--btn-orange-light), var(--btn-orange));
    border-radius: 2px; color: #fff; text-align: center;
    font-family: "Oswald", sans-serif; font-size: 21px; line-height: 47px; letter-spacing: -0.3px;
  }

  .benefits {
    position: absolute; left: 489px; top: 274px; width: 623px; height: 319px;
    background: var(--benefits-blue); color: #fff;
  }
  .benefits h2 {
    position: absolute; left: 45px; top: 32px;
    font-family: "Oswald", sans-serif; font-weight: 400; font-size: 33px; letter-spacing: -0.5px; line-height: 1;
  }
  .benefits ul { position: absolute; left: 45px; top: 88px; list-style: none; }
  .benefits li {
    font-family: "Oswald", sans-serif; font-size: 15.5px; letter-spacing: -0.4px;
    height: 35px; line-height: 22px; white-space: nowrap;
  }
  .benefits li::before { content: "»"; margin-right: 7px; font-family: "Roboto", sans-serif; }

  .site-footer {
    position: absolute; left: 0; top: 722px; width: 1200px; height: 115px;
    background: linear-gradient(#fafafa, var(--footer-bg));
  }
  .footer-links { position: absolute; left: 90px; top: 33px; font-size: 13px; color: var(--text-dark); }
  .footer-links .sep { margin: 0 6px; }
  .copyright { position: absolute; left: 90px; top: 60px; font-size: 15px; color: var(--text-dark); }
  .social { position: absolute; left: 953px; top: 45px; display: flex; gap: 11px; }
  .social span { width: 33px; height: 33px; background: var(--social-grey); border-radius: 2px; display: block; }
</style>
</head>
<body>
  <header class="site-header">
    <div class="brand">VENUORA</div>
    <nav class="main-nav">FIND<span class="sep">|</span>EVENTS</nav>
    <div class="search-box">
      <span>Search</span>
      <svg width="20" height="20" viewBox="0 0 20 20" aria-hidden="true">
        <circle cx="8" cy="8" r="6" fill="none" stroke="#222" stroke-width="2"/>
        <line x1="12.5" y1="12.5" x2="18" y2="18" stroke="#222" stroke-width="3" stroke-linecap="round"/>
      </svg>
    </div>
    <div class="header-btn signup">SIGN UP</div>
    <div class="header-btn login">LOGIN</div>
  </header>

  <section class="hero" role="img" aria-label="Concert crowd with raised hands under stage lights"></section>

  <form class="signup-panel">
    <div class="panel-title">SIGN UP</div>
    <div class="field invalid" style="top:79px">User Name</div>
    <div class="error-msg" style="top:92px"><b>X</b>Error message</div>
    <div class="field" style="top:129px">Email Address</div>
    <div class="error-msg" style="top:143px"><b>X</b>Error message</div>
    <div class="field" style="top:179px;padding-top:17px">Password</div>
    <div class="field" style="top:229px">Confirm Password</div>
    <div class="field" style="top:278px">First Name</div>
    <div class="field" style="top:328px">Last Name</div>
    <div class="field" style="top:378px">Date of birth</div>
    <div class="submit-btn">SIGN UP NOW</div>
  </form>

  <section class="benefits">
    <h2>BNEFITS</h2>
    <ul>
      <li>GET PERSONALISED EVENT RECOMMENDATIONS</li>
      <li>GET NOTIFIED ABOUT YOUR FAVOURITE EVENTS - NEVER MISS OUT AGAIN</li>
      <li>FOLLOW ALL YOUR FAVOURITE ARTISTS, MUSICIANS, TEAMS AND PLAYERS IN ONE PLACE</li>
      <li>FOLLOW YOUR FAVOURITE LOCAL VENUES TO KNOW EVERYTHING HAPPENING THERE</li>
      <li>GET CURATED NEWS AND FEATURE CONTENT ON YOUR FAVOURITE ARTISTS (COMING SOON)</li>
      <li>INVITE YOUR MATES TO EVENTS VIA CIRCLEBOOK (CB SIGN-UP ONLY)</li>
    </ul>
  </section>

  <footer class="site-footer">
    <div class="footer-links">About<span class="sep">|</span>Disclaimer<span class="sep">|</span>Contact<span class="sep">|</span>Sitemap<span class="sep">|</span>Hosted Solutions Partner</div>
    <div class="copyright">Copyright © 2015&nbsp; All Rights</div>
    <div class="social" aria-label="Social links">
      <span></span><span></span><span></span><span></span>
    </div>
  </footer>
</body>
</html>
```